Calden L - Premium Business Cards

Background of Calden L
Calden Leafworks is a cigar mobile lounge where guests become family. A place of luxury, relaxation, and ambiance is the global popularity demand. Calden Leafworks strives to provide first-class service of quality and products. Our goal is to ensure that every guest is treated and serviced as a VIP.

Calden Leafworks was founded by Dennis Markow Jr in January 2020. After 15 years of cigar reviews and research Dennis decided it was time to launch his own cigar brand and boutique cigar company. With a wealth of knowledge and years of experience Calden Leafworks was born. With opulence for all cultures, Calden Leafworks offers hand rolled cigars with premium blend tobacco from sweet to bold imported from Costa Rica, Dominican Republic, and Nicaragua. Thank you for your business!

Objective:
Create a business card template to be used for all employees. Design should communicate premium and classy. And should use earth tone colors.

Design should include:
1. Client wants to incorporate the cigar leaf
2. Logo
3. Tagline: Respect the smoke
3. Content info:
Kevin Oldacre
Owner
555-017-4863
koldacre@caldenleaf.com
caldenleafworks.com

```html
<!DOCTYPE html>
<html lang="en">
<head>
<meta charset="utf-8">
<title>Calden Leafworks – Business Card</title>
<link href="https://fonts.googleapis.com/css2?family=Josefin+Sans:wght@700&family=Roboto+Condensed:wght@400;700&display=swap" rel="stylesheet">
<style>
  :root {
    --bg: #1c1c1e;
    --leaf-dark: #2e1c10;
    --leaf-mid: #6b4428;
    --leaf-light: #9a6a43;
    --paper: #f6f5f2;
    --ink: #1a1a1a;
    --ink-soft: #444;
    --white: #ffffff;
  }
  * { margin: 0; padding: 0; box-sizing: border-box; }
  html, body { width: 1200px; height: 874px; overflow: hidden; background: var(--bg); }
  .canvas {
    width: 1200px; height: 874px;
    display: flex; flex-direction: column; align-items: center; justify-content: center; gap: 26px;
  }
  .card { position: relative; width: 700px; height: 400px; overflow: hidden; }

  /* Front */
  .card-front { background: var(--leaf-dark); }
  .leaf-photo {
    position: absolute; inset: 0;
    background: radial-gradient(ellipse at 45% 40%, var(--leaf-light) 0%, var(--leaf-mid) 40%, var(--leaf-dark) 100%);
  }
  .frame { position: absolute; inset: 16px; }
  .frame-front { border: 1.5px solid rgba(255,255,255,0.75); }
  .frame-back { border: 2px solid var(--ink); inset: 18px; }
  .corner { position: absolute; width: 9px; height: 9px; border-radius: 50%; }
  .frame-front .corner { background: rgba(255,255,255,0.85); }
  .frame-back .corner { background: var(--ink); }
  .corner.tl { top: -5px; left: -5px; } .corner.tr { top: -5px; right: -5px; }
  .corner.bl { bottom: -5px; left: -5px; } .corner.br { bottom: -5px; right: -5px; }
  .lockup {
    position: absolute; left: 60px; right: 60px; top: 148px;
    display: flex; flex-direction: column; align-items: center; gap: 16px;
  }
  .brand {
    font-family: "Josefin Sans", sans-serif; font-weight: 700;
    color: var(--white); font-size: 42px; letter-spacing: 3px; line-height: 1;
    text-transform: uppercase; white-space: nowrap;
  }
  .tagline {
    display: flex; align-items: center; gap: 12px;
    font-family: "Roboto Condensed", sans-serif; font-weight: 400;
    color: var(--white); font-size: 15px; letter-spacing: 3px; text-transform: uppercase;
  }
  .tagline::before, .tagline::after {
    content: ""; width: 90px; height: 1px; background: rgba(255,255,255,0.8);
  }

  /* Back */
  .card-back { background: var(--paper); color: var(--ink); font-family: "Roboto Condensed", sans-serif; }
  .holder { position: absolute; left: 110px; top: 172px; text-align: right; width: 280px; }
  .holder-name { font-weight: 700; font-size: 31px; letter-spacing: 0.3px; text-transform: uppercase; line-height: 1.1; }
  .holder-role { font-size: 13px; color: var(--ink-soft); margin-top: 4px; }
  .brand-dot { position: absolute; left: 408px; top: 180px; width: 16px; height: 16px; border-radius: 50%; background: var(--ink); }
  .contacts { position: absolute; left: 440px; top: 202px; list-style: none; font-size: 17px; line-height: 24px; }
  .contacts li { display: flex; align-items: center; gap: 8px; }
  .contacts svg { width: 13px; height: 13px; fill: var(--ink); flex: none; }
  .contacts .web { font-weight: 700; }
  .contacts .web span { font-weight: 400; }
</style>
</head>
<body>
<main class="canvas">
  <section class="card card-front">
    <div class="leaf-photo" role="img" aria-label="Close-up photograph of dried cigar tobacco leaves"></div>
    <div class="frame frame-front">
      <span class="corner tl"></span><span class="corner tr"></span>
      <span class="corner bl"></span><span class="corner br"></span>
    </div>
    <div class="lockup">
      <h1 class="brand">Calden Leafworks</h1>
      <p class="tagline">Respect the smoke</p>
    </div>
  </section>

  <section class="card card-back">
    <div class="frame frame-back">
      <span class="corner tl"></span><span class="corner tr"></span>
      <span class="corner bl"></span><span class="corner br"></span>
    </div>
    <div class="holder">
      <p class="holder-name">Kevin Oldacre</p>
      <p class="holder-role">Owner</p>
    </div>
    <span class="brand-dot"></span>
    <ul class="contacts">
      <li>
        <svg viewBox="0 0 24 24" aria-hidden="true"><path d="M6.6 10.8a15 15 0 0 0 6.6 6.6l2.2-2.2a1 1 0 0 1 1-.25 11.4 11.4 0 0 0 3.6.57 1 1 0 0 1 1 1V20a1 1 0 0 1-1 1A17 17 0 0 1 3 4a1 1 0 0 1 1-1h3.5a1 1 0 0 1 1 1c0 1.25.2 2.45.57 3.6a1 1 0 0 1-.25 1z"/></svg>
        555-017-4863
      </li>
      <li>
        <svg viewBox="0 0 24 24" aria-hidden="true"><path d="M2 5h20v14H2z M4 7v.5l8 5 8-5V7l-8 5z" fill-rule="evenodd"/></svg>
        koldacre@caldenleaf.com
      </li>
      <li class="web">
        <svg viewBox="0 0 24 24" aria-hidden="true"><circle cx="12" cy="12" r="10"/></svg>
        <p>caldenleafworks<span>.com</span></p>
      </li>
    </ul>
  </section>
</main>
</body>
</html>
```